Overseas Property Tax Depreciation

We need a two sided flyer to promote our business and explain what we do. our website is www.dorwix.net.
The attached word file is what I would like on an A5 size flyer with one side showing the FAQ and the other the worked example. I would like these formatted much better than the are and in general style of the website. I will attach files for logos as well.

```html
<!DOCTYPE html>
<html lang="en">
<head>
<meta charset="utf-8">
<title>Overseas Property Tax Depreciation – FAQ</title>
<link href="https://fonts.googleapis.com/css2?family=Didact+Gothic&family=Mulish:wght@700;800&display=swap" rel="stylesheet">
<style>
  :root{
    --backdrop:#3a2a1e;
    --navy:#2a2a6e;
    --navy-dark:#1d1d55;
    --sky-top:#1f63b8;
    --sky-mid:#3f8fdc;
    --sky-light:#a9cdf0;
    --panel:#f4f6f9;
    --panel-shade:#e3e8ef;
    --ink:#1c1c1c;
    --link:#1a3cc8;
    --white:#ffffff;
  }
  *{margin:0;padding:0;box-sizing:border-box}
  html,body{width:863px;height:1200px;overflow:hidden;background:var(--backdrop)}
  .flyer{
    position:absolute;left:42px;top:47px;width:778px;height:1105px;
    background:linear-gradient(180deg,var(--panel) 0%,var(--panel-shade) 55%,var(--panel) 100%);
    font-family:"Didact Gothic",sans-serif;color:var(--ink);overflow:hidden;
  }
  .hero{
    position:absolute;left:0;top:0;width:778px;height:160px;
    background:linear-gradient(90deg,var(--sky-top) 0%,var(--sky-mid) 30%,var(--sky-light) 55%,var(--sky-mid) 75%,#5b7fb0 100%);
  }
  .brand{
    position:absolute;left:262px;top:42px;display:flex;align-items:center;gap:14px;
  }
  .brand-dot{width:64px;height:64px;border-radius:50%;background:var(--white)}
  .brand-name{font-family:"Didact Gothic",sans-serif;font-size:50px;color:var(--white);letter-spacing:1px}
  .content{position:absolute;left:28px;top:160px;width:726px;height:920px;background:rgba(255,255,255,.55)}
  .section{position:absolute;left:0;width:726px}
  .tab{
    display:flex;align-items:center;height:28px;padding-left:22px;
    background:
      linear-gradient(90deg,var(--navy) 0 3px,transparent 3px 6px,var(--navy) 6px 9px,transparent 9px 12px,var(--navy) 12px 15px,transparent 15px) left/16px 100% no-repeat,
      linear-gradient(var(--navy),var(--navy)) 17px 0/100% 100% no-repeat;
    clip-path:polygon(0 0,calc(100% - 12px) 0,100% 50%,calc(100% - 12px) 100%,0 100%);
    color:var(--white);font-family:"Mulish",sans-serif;font-weight:800;font-size:17px;
  }
  .tab span{padding-left:2px}
  .tab.tall{height:50px;line-height:22px}
  .body{padding:0 26px 0 18px;font-size:13.4px;line-height:16px;text-align:justify}
  .body p{margin-top:9px}
  .body ul{list-style:none;margin-top:8px}
  .body li{position:relative;padding-left:24px;margin-bottom:2px}
  .body li::before{content:"";position:absolute;left:2px;top:6px;width:5px;height:5px;border-radius:50%;background:var(--navy-dark)}
  .body .fees li{padding-left:30px;margin-bottom:10px}
  .body .fees li::before{width:7px;height:7px;top:4px}
  .link{color:var(--link)}
  .tax-figure{
    position:absolute;left:640px;top:645px;width:86px;height:140px;
    background:radial-gradient(ellipse at 50% 60%,rgba(200,60,50,.35),rgba(230,230,230,.1) 70%);
  }
</style>
</head>
<body>
<main class="flyer">
  <div class="hero" role="img" aria-label="City skyline of office towers beside a close-up of a tax calculator keypad"></div>
  <div class="brand"><span class="brand-dot"></span><span class="brand-name">CQSI</span></div>

  <div class="content">
    <section class="section" style="top:5px">
      <h2 class="tab" style="width:158px"><span>Why use us?</span></h2>
      <div class="body">
        <p>There are several websites out there offering tax depreciation reports for Australian properties but there are very few who are appropriately qualified and approved by the Australian Tax Office (ATO) and offer the necessary Irish expertise. The Quantity Surveyor that prepares your report:</p>
        <ul>
          <li>is Irish and qualified as a Quantity Surveyor in Ireland.</li>
          <li>worked there during the "Celtic Tiger" period when construction costs were quite high.</li>
          <li>has detailed knowledge of Irish construction methods and costs over the past 20 years. Irish buildings are generally much more expensive than Australia due to the climate, just think about how many Australian houses you have seen that have double glazing, central heating, insulation etc..</li>
          <li>has a partnership arrangement with an Irish quantity surveying firm to carry out the property inspections required in most cases to maximize the deductions available.</li>
          <li>is a chartered member of the CQSI.</li>
          <li>Maintains the Appropriate Professional Indemnity Insurance.</li>
          <li>Is registered with the Tax Practitioners Board. All quantity surveyors who prepare Property Tax Depreciation Schedules are required by the ATO to be registered with the Tax Practitioners Board which checks that the person preparing the reports is suitably qualified and maintains the appropriate professional indemnity insurance. You can check the registration on the <span class="link">TPB website</span>.</li>
          <li>Our registration number is 31847265.</li>
        </ul>
      </div>
    </section>

    <section class="section" style="top:339px">
      <h2 class="tab" style="width:518px"><span>My property is in Ireland does this make a difference?</span></h2>
      <div class="body">
        <p>Division 43 of the Income Tax Assessment Act 1997 which deals with capital works depreciation states that it applies to buildings begun outside Australia after 21 August 1990 Sect 43.20 (1) (b). Your Australian tax return should cover your worldwide income. As long as the property is available to rent back in Ireland you are obliged by the ATO to report any income or loss on that property.</p>
      </div>
    </section>

    <section class="section" style="top:443px">
      <h2 class="tab" style="width:266px"><span>Is my property too old?</span></h2>
      <div class="body">
        <p>No, if your property was constructed after 1990 you can claim for both the construction cost element and the Plant and equipment. If it was built before then you can still claim the plant and equipment allowance. The easiest thing to do is to contact us with some details on your property and we can make an initial assessment of the possible annual savings.</p>
      </div>
    </section>

    <div class="tax-figure" role="img" aria-label="Small illustrated figure pulling a rope attached to the word TAX"></div>

    <section class="section" style="top:551px">
      <h2 class="tab" style="width:345px"><span>What is Property Depreciation?</span></h2>
      <div class="body">
        <p style="padding-right:40px">Just like you claim wear and tear on a car purchased for income producing purposes, you can also claim the depreciation of your investment property against your taxable income.</p>
        <p>There are 2 types available: depreciation on Plant and Equipment, and depreciation on the cost of construction. Plant and Equipment refers to items within the building like ovens, dishwashers, carpet and blinds etc. Both these costs can be offset against your assessable income.</p>
      </div>
    </section>

    <section class="section" style="top:686px">
      <h2 class="tab" style="width:333px"><span>How much will the report cost?</span></h2>
      <div class="body">
        <p>Each scenario is different so contact us to obtain a quick quote for your situation. Generally the cost of the report is a fraction of the savings in any one year.</p>
        <ul class="fees">
          <li>Our fee is fully tax deductible</li>
          <li>You do NOT need to get this report done every year so the cost can be spread over several years</li>
        </ul>
      </div>
    </section>

    <section class="section" style="top:811px">
      <h2 class="tab tall" style="width:678px"><span>I haven't included my property for the past couple of years on my tax<br>return is this a problem?</span></h2>
      <div class="body">
        <p style="text-align:left">No, in actual fact you could have been missing out on savings for a number of years,<br>you can also use this report to claim a refund from the ATO for up to the past three years.</p>
      </div>
    </section>
  </div>
</main>
</body>
</html>
```